full stationary design for a modern sleek design company

we are a design company that does modern minimalistic interior design works as well as other design services for high end clients.
we need a full stationary design including and not limited to (double sided business card, letter head, envelopes, documents folder...etc) that reflects the modern style design we do.
sleek modern and minimalistic is the requirements.
Updates

please use the latest attached files as there was a slight modification on the logo Added Wednesday, March 1, 2017

minor update on the logo files in JPG and PSD has been updated kindly follow the new attachments. Added Thursday, March 2, 2017

Target Market(s)

modern minimalist clients

Industry/Entity Type

Design Agency

Requirements
Must have
• the logo
Nice to have
• i like the colors in the colored 3D logo attached
Should not have
• too many colors

```html
<!DOCTYPE html>
<html lang="en">
<head>
<meta charset="utf-8">
<title>Norde Atelier – Business Card</title>
<link rel="stylesheet" href="https://fonts.googleapis.com/css2?family=Open+Sans:wght@400;600;700&display=swap">
<style>
  :root {
    --orange: #f7941e;
    --charcoal: #3a3a3a;
    --text: #4a4a4a;
    --white: #ffffff;
    --backdrop: #e7e4df;
  }
  * { margin: 0; padding: 0; box-sizing: border-box; }
  html, body {
    width: 1200px;
    height: 987px;
    overflow: hidden;
    background: var(--backdrop);
    font-family: "Open Sans", Arial, sans-serif;
  }
  .stage { position: relative; width: 1200px; height: 987px; }

  .card {
    position: absolute;
    left: 293px;
    width: 615px;
    height: 349px;
    box-shadow: 0 3px 10px rgba(0,0,0,0.18);
  }
  .card--front {
    top: 131px;
    background: var(--white);
    border-top-left-radius: 47px;
  }
  .card--back {
    top: 506px;
    background: var(--orange);
    border-top-right-radius: 47px;
  }

  .brand {
    position: absolute;
    display: flex;
    align-items: center;
    gap: 12px;
    font-weight: 600;
    text-transform: uppercase;
    letter-spacing: 2px;
    white-space: nowrap;
  }
  .brand__mark { display: block; }
  .card--front .brand {
    left: 50px;
    top: 48px;
    font-size: 29px;
    color: var(--charcoal);
  }
  .card--front .brand__mark { width: 16px; height: 16px; background: var(--orange); }
  .card--back .brand {
    left: 0;
    right: 0;
    top: 150px;
    justify-content: center;
    font-size: 31px;
    color: var(--white);
  }
  .card--back .brand__mark { width: 20px; height: 20px; background: var(--white); }

  .person { position: absolute; left: 48px; top: 110px; }
  .person__name {
    font-size: 21px;
    font-weight: 700;
    color: var(--orange);
    line-height: 1.1;
  }
  .person__role {
    font-size: 16px;
    color: var(--charcoal);
    margin-top: 3px;
  }

  .address {
    position: absolute;
    left: 48px;
    top: 168px;
    font-style: normal;
    font-size: 15px;
    line-height: 23px;
    color: var(--text);
  }

  .contacts {
    position: absolute;
    left: 48px;
    top: 219px;
    list-style: none;
    font-size: 15px;
    color: var(--text);
  }
  .contacts li {
    display: flex;
    align-items: center;
    gap: 8px;
    height: 23.5px;
  }
  .contacts svg { width: 14px; height: 14px; fill: var(--orange); flex: none; }

  .side-block {
    position: absolute;
    left: 440px;
    top: 15px;
    width: 158px;
    height: 320px;
    background: var(--orange);
  }
</style>
</head>
<body>
<main class="stage">

  <section class="card card--front" aria-label="Business card front">
    <div class="brand"><span class="brand__mark"></span>Norde Atelier</div>

    <div class="person">
      <p class="person__name">MAREK OLSEN</p>
      <p class="person__role">CEO&amp;Founder</p>
    </div>

    <address class="address">
      2140 Larchwood Avenue<br>
      Juneau, Alaska 99801
    </address>

    <ul class="contacts">
      <li>
        <svg viewBox="0 0 16 16" aria-hidden="true"><path d="M3.6 1.2l2.4 2.6-1.3 2c.9 1.9 2.5 3.5 4.5 4.5l2-1.3 2.6 2.4-1.4 2.4C6.5 13.4 2.6 9.5 1.2 3.6z"/></svg>
        (555) 214 7390
      </li>
      <li>
        <svg viewBox="0 0 16 16" aria-hidden="true"><path d="M4.5 0h7a1 1 0 0 1 1 1v14a1 1 0 0 1-1 1h-7a1 1 0 0 1-1-1V1a1 1 0 0 1 1-1zm.6 2v10h5.8V2zM8 12.8a.9.9 0 1 0 0 1.8.9.9 0 0 0 0-1.8z"/></svg>
        (555) 862 4017
      </li>
      <li>
        <svg viewBox="0 0 16 16" aria-hidden="true"><path d="M1 3h14v1.2L8 8.6 1 4.2zm0 2.6l7 4.4 7-4.4V13H1z"/></svg>
        marek@nordeatelier.com
      </li>
      <li>
        <svg viewBox="0 0 16 16" aria-hidden="true"><path d="M8 1a7 7 0 1 0 0 14A7 7 0 0 0 8 1zm-1 2.3c-.8.8-1 1.8-.4 2.5.6.7 1.8.3 2.2 1.2.3.8-.6 1.4-.2 2.3.3.6 1 .6 1.2 1.6.1.6-.1 1.4-.7 2A5.4 5.4 0 0 1 7 3.3zm4.2 1.4a5.4 5.4 0 0 1 1.9 5.6c-.7-.2-1.1-.9-1.6-1.6-.6-.8-.2-2.2-.5-3.1-.1-.4.1-.7.2-.9z"/></svg>
        www.nordeatelier.com
      </li>
    </ul>

    <div class="side-block" role="img" aria-label="Brand colour block"></div>
  </section>

  <section class="card card--back" aria-label="Business card back">
    <div class="brand"><span class="brand__mark"></span>Norde Atelier</div>
  </section>

</main>
</body>
</html>
```